Tandem Hearth Works Pty Ltd

We need business cards for a company based in Perth, we install, service and maintain fire equipment.
On the front we want a great design with our logo and a small spot for our full company name, general company email address and office number. On the back we need space for our name, title, mobile number and email address on the back.

Target Market(s)

Facility managers and commercial/industrial building owners/occupiers.

Contact Information for Business Card

Font styles to use
Sans Serif

Requirements
Must have
• Please only submit 5 of your best samples.
Darker tones are preferred.
Nice to have
• We want to use, black, red and grey. Keep it modern and clean.
I've attached the company logo and a sample of a boarder we use on our emergency plans.
Should not have
• No preference. Let the designer choose.

```html
<!DOCTYPE html>
<html lang="en">
<head>
<meta charset="utf-8">
<title>Tandem Hearth Works – Business Card</title>
<link href="https://fonts.googleapis.com/css2?family=Roboto:wght@400;700&display=swap" rel="stylesheet">
<style>
  :root {
    --brand-red: #ec1c24;
    --card-white: #f5f3f3;
    --backdrop: #dcd8d7;
    --text-light: #ffffff;
  }
  * { margin: 0; padding: 0; box-sizing: border-box; }
  html, body {
    width: 1200px; height: 900px; overflow: hidden;
    background: var(--backdrop);
    font-family: "Roboto", Arial, sans-serif;
  }
  .card {
    position: absolute; left: 150px; top: 171px;
    width: 900px; height: 557px;
    background: var(--card-white);
    box-shadow: 0 12px 40px rgba(0,0,0,0.12);
    display: flex;
  }
  .card__info {
    position: relative;
    width: 444px; height: 100%;
    background: var(--brand-red);
    color: var(--text-light);
  }
  .card__info > * { position: absolute; left: 38px; white-space: nowrap; }
  .person-name { top: 62px; font-size: 36px; font-weight: 700; letter-spacing: 0.2px; }
  .person-title { top: 100px; font-size: 26px; font-weight: 400; }
  .contact-line {
    display: flex; align-items: center; gap: 14px;
    font-size: 25px; font-weight: 400;
  }
  .contact-line svg { width: 24px; height: 24px; flex: none; }
  .contact-mobile { top: 152px; }
  .contact-email { top: 185px; }
  .company-name {
    top: 264px; font-size: 36px; font-weight: 700; line-height: 40px;
  }
  .office-phone { top: 396px; font-size: 38px; font-weight: 700; }
  .contact-info { top: 449px; }
  .contact-web { top: 482px; }
  .card__brand {
    flex: 1; display: flex; align-items: center; justify-content: center;
  }
  .brand-name {
    color: var(--brand-red);
    font-size: 150px; font-weight: 700; letter-spacing: -2px;
    line-height: 1;
  }
</style>
</head>
<body>
  <div class="card">
    <section class="card__info">
      <div class="person-name">MARCUS DELANEY</div>
      <div class="person-title">Managing Director</div>

      <div class="contact-line contact-mobile">
        <svg viewBox="0 0 24 24" aria-hidden="true"><rect x="6" y="2" width="12" height="20" rx="2" fill="none" stroke="#fff" stroke-width="2"/><circle cx="12" cy="18.5" r="1.3" fill="#fff"/><line x1="10" y1="4.5" x2="14" y2="4.5" stroke="#fff" stroke-width="1.4"/></svg>
        <span>789.5550.4821</span>
      </div>
      <div class="contact-line contact-email">
        <svg viewBox="0 0 24 24" aria-hidden="true"><rect x="2" y="6" width="20" height="13" fill="#fff"/><path d="M2 6 L12 14 L22 6" fill="none" stroke="#ec1c24" stroke-width="1.6"/></svg>
        <span>name@thw.com</span>
      </div>

      <div class="company-name">TANDEM HEARTH<br>WORKS<br>PTY LTD</div>
      <div class="office-phone">789.5550.2100</div>

      <div class="contact-line contact-info">
        <svg viewBox="0 0 24 24" aria-hidden="true"><rect x="2" y="6" width="20" height="13" fill="#fff"/><path d="M2 6 L12 14 L22 6" fill="none" stroke="#ec1c24" stroke-width="1.6"/></svg>
        <span>info@thw.com</span>
      </div>
      <div class="contact-line contact-web">
        <svg viewBox="0 0 24 24" aria-hidden="true"><g fill="none" stroke="#fff" stroke-width="1.6"><circle cx="12" cy="12" r="10"/><ellipse cx="12" cy="12" rx="4.5" ry="10"/><line x1="2" y1="12" x2="22" y2="12"/><path d="M4 7 H20 M4 17 H20"/></g></svg>
        <span>www.thw.com</span>
      </div>
    </section>

    <section class="card__brand">
      <div class="brand-name">THW</div>
    </section>
  </div>
</body>
</html>
```